Fire Risk Assessment App needs a sleek UI design

I need a sleek, modern but professional design for my 5 page Fire Risk Assessment App. Include gradient background, fire themed colours including reds, yellows, light orange and a touch of black. Design must ooze simplicity and professionalism. This is for the UK market. See attached images and word doc for more information.

Target Market(s)

General public and business owners

Industry/Entity Type

Technology / Fire Safety

Colors
00AB8E
00BBA5
67D7C9
C6EFE9
E9F9F6
59FF00
82FF00
B8FF75
E3FFCB
F4FFEA
FFC000
F8CF3A
FAE287
FDF2CF
FEFAEE
F0912C
F2A743
F7CA91
FBE8D2
FDF5EE
EE7325
F08F49
F5BC92
FAE3D3
FDF4ED
EB3D1F
EC4F4E
F09395
F8D3D4
FCEDEE

```html
<!DOCTYPE html>
<html lang="en">
<head>
<meta charset="utf-8">
<title>Fire Risk Assessment App – Screens</title>
<link href="https://fonts.googleapis.com/css2?family=Montserrat:wght@400;500;600;700&display=swap" rel="stylesheet">
<style>
:root{
  --bg-top:#fdf8f1;
  --bg-bottom:#f6efef;
  --screen-top:#f3ece6;
  --screen-mid:#f1f1e2;
  --screen-low:#f3e2e2;
  --screen-bottom:#ebe6e6;
  --ink:#111111;
  --muted:#6a6a6a;
  --card:#f7f6f5;
  --line:#e3e0dc;
  --orange:#f2a743;
  --orange-soft:#f7ca91;
  --red:#eb3d1f;
  --red-soft:#ec4f4e;
  --yellow:#ffc000;
  --green:#2d9a2d;
  --blue:#2f7de1;
}
*{box-sizing:border-box;margin:0;padding:0}
html,body{width:1200px;height:771px;overflow:hidden}
body{
  font-family:"Montserrat",sans-serif;
  color:var(--ink);
  background:linear-gradient(180deg,var(--bg-top),var(--bg-bottom));
  position:relative;
}
.screen{
  position:absolute;top:68px;width:285px;height:613px;border-radius:30px;overflow:hidden;
  background:linear-gradient(180deg,var(--screen-top) 0%,var(--screen-mid) 45%,var(--screen-low) 75%,var(--screen-bottom) 100%);
  box-shadow:0 6px 22px rgba(0,0,0,.08);
}
.screen--intro{left:75px}
.screen--dashboard{left:460px}
.screen--support{left:845px}
.abs{position:absolute}

/* intro */
.intro-heading{left:0;width:100%;top:37px;text-align:center;font-size:13.5px;line-height:20px;font-weight:500}
.intro-heading b{font-weight:700}
.paper-back{left:46px;top:108px;width:70px;height:200px;background:#fbfbfa;border:1px solid var(--line);border-radius:6px;transform:rotate(-8deg)}
.paper-back.two{left:58px;top:104px;transform:rotate(-5deg)}
.sheet{left:92px;top:90px;width:149px;height:217px;background:var(--card);border:1px solid var(--line);border-radius:6px;padding:10px 9px;font-size:6px}
.sheet .t1{font-size:8px;font-weight:600}
.sheet .t2{font-size:5.5px;margin-top:6px;color:#333}
.sheet .t3{font-size:7px;font-weight:600;margin-top:7px}
.sheet .t4{font-size:5.5px;margin-top:6px;color:#333}
.sheet .dots{position:absolute;right:7px;top:12px;display:flex;flex-direction:column;gap:6px}
.sheet .dots i{width:6px;height:6px;border-radius:50%;background:var(--orange)}
.sheet .bolt{position:absolute;left:68px;top:75px}
.sheet .q{position:absolute;left:9px;top:100px;font-size:8px;font-weight:500}
.sheet .qtext{position:absolute;left:9px;top:116px;width:130px;font-size:6px;line-height:10px}
.sheet .answers{position:absolute;left:11px;top:143px;display:flex;gap:9px;align-items:center}
.sheet .lorem{position:absolute;left:9px;top:168px;width:136px;font-size:6px;line-height:10px}
.sheet .photo-btn{position:absolute;left:47px;top:193px;width:55px;height:18px;background:var(--orange);color:#fff;font-size:8px;display:flex;align-items:center;justify-content:center;font-weight:500}
.tagline{left:0;width:100%;text-align:center;font-size:11px;font-weight:500}
.tagline b{font-weight:700}
.rule{width:30px;height:1.5px;background:var(--orange);left:127px}
.action-box{left:60px;width:164px;background:var(--card);border-radius:4px;display:flex;flex-direction:column;align-items:center;font-size:11px;font-weight:500}
.action-box--create{top:365px;height:59px;padding-top:8px;gap:3px}
.action-box--login{top:470px;height:90px;padding-top:8px;gap:3px}
.credit{left:0;width:100%;top:573px;text-align:center;font-size:12px;font-weight:700}

/* header */
.screen-title{top:28px;font-size:17px;font-weight:600;letter-spacing:.3px}
.title-badge{width:32px;height:32px;border-radius:50%;background:var(--orange);display:flex;align-items:center;justify-content:center;top:21px}

/* dashboard */
.node{border-radius:50%;background:#f7f5f3;box-shadow:0 2px 6px rgba(0,0,0,.08);display:flex;align-items:center;justify-content:center}
.node--start{left:122px;top:64px;width:58px;height:58px}
.node--commercial{left:47px;top:141px;width:58px;height:58px}
.node--residential{left:198px;top:141px;width:58px;height:58px}
.node-label{font-size:9px;font-weight:600;text-align:center;width:120px}
.status-pill{left:10px;width:131px;height:26px;border-radius:14px;background:#f7f5f3;box-shadow:0 1px 3px rgba(0,0,0,.08);display:flex;align-items:center;justify-content:space-between;padding:0 17px;font-size:8.5px;font-weight:600}
.entry{left:14px;font-size:8px;display:flex;align-items:center;gap:7px;transform:translateY(-50%)}
.entry::before{content:"";width:6px;height:6px;border:1.3px solid var(--ink);border-radius:50%}
.tab-bar{left:0;bottom:0;width:100%;height:36px;background:#f2efee}
.tab{transform:translate(-50%,-50%);display:flex;align-items:center;justify-content:center}
.tab--active{width:36px;height:36px;border-radius:50%;background:var(--orange)}

/* support */
.reply-box{left:10px;top:77px;width:258px;height:167px;background:#f4f3f2;border-radius:4px;box-shadow:0 1px 4px rgba(0,0,0,.08);padding:13px 13px;font-size:7.5px;color:var(--muted)}
.reply-box svg{position:absolute;right:12px;top:14px}
.send-btn{left:191px;top:255px;width:70px;height:23px;background:var(--orange);color:#fff;font-size:10px;font-weight:600;display:flex;align-items:center;justify-content:center;border-radius:2px}
</style>
</head>
<body>

<!-- Screen 1: intro -->
<section class="screen screen--intro">
  <p class="abs intro-heading">The most <b>‘user friendly’</b> Fire Risk<br>Assessment App available.</p>
  <div class="abs paper-back"></div>
  <div class="abs paper-back two"></div>
  <div class="abs sheet">
    <div class="dots"><i></i><i></i></div>
    <p class="t1">FIRE RISK ASSESSMENT</p>
    <p class="t2">FIRE HAZARDS</p>
    <p class="t3">SECTION 7-00/30-00</p>
    <p class="t4">ELECTRONIC SOURCES OF IGNITION</p>
    <svg class="bolt" width="12" height="22" viewBox="0 0 12 22"><path d="M7 0 1 12h4l-2 10 8-13H7l3-9z" fill="var(--red)"/></svg>
    <p class="q">Q: 7:01</p>
    <p class="qtext">Are reasonable measures taken do prevent fires of electrical origin?</p>
    <div class="answers">
      <svg width="14" height="12" viewBox="0 0 14 12"><path d="M1 6l4 4 8-9" stroke="var(--green)" stroke-width="2.4" fill="none"/></svg>
      <svg width="13" height="13" viewBox="0 0 13 13"><circle cx="6.5" cy="6.5" r="6.5" fill="var(--red-soft)"/><path d="M4 4l5 5M9 4l-5 5" stroke="#fff" stroke-width="1.6"/></svg>
      <svg width="13" height="13" viewBox="0 0 13 13"><circle cx="6.5" cy="6.5" r="6.5" fill="var(--yellow)"/><path d="M3.5 6.5h6" stroke="#fff" stroke-width="1.8"/></svg>
      <svg width="15" height="12" viewBox="0 0 15 12"><rect x="0.5" y="2" width="14" height="10" rx="2" fill="#4a8fd0"/><circle cx="7.5" cy="7" r="3" fill="#fff"/><circle cx="7.5" cy="7" r="1.6" fill="#333"/></svg>
      <svg width="13" height="13" viewBox="0 0 13 13"><circle cx="6.5" cy="6.5" r="6.5" fill="var(--red-soft)"/><rect x="5" y="3" width="3" height="5" rx="1.5" fill="#fff"/><path d="M6.5 8v2" stroke="#fff"/></svg>
    </div>
    <p class="lorem">Lorem ipsum dolor sit amet, consectetur adipiscing elit,</p>
    <div class="photo-btn">Photo</div>
  </div>

  <p class="abs tagline" style="top:330px">Quick tap <b>responses and voice activated</b> typing</p>
  <div class="abs rule" style="top:351px"></div>

  <div class="abs action-box action-box--create">
    <svg width="22" height="24" viewBox="0 0 22 24"><circle cx="9" cy="6" r="4.5" fill="none" stroke="#111" stroke-width="1.6"/><path d="M1 21c0-5 4-8 8-8s6 2 7 4" fill="none" stroke="#111" stroke-width="1.6"/><circle cx="16.5" cy="18.5" r="4.5" fill="var(--green)"/><path d="M16.5 16v5M14 18.5h5" stroke="#fff" stroke-width="1.4"/></svg>
    <span>Create a Free account</span>
  </div>

  <p class="abs tagline" style="top:439px">Any <b>Responsible Person</b> can do it.</p>
  <div class="abs rule" style="top:457px"></div>

  <div class="abs action-box action-box--login">
    <svg width="22" height="24" viewBox="0 0 22 24"><circle cx="9" cy="6" r="4.5" fill="none" stroke="#111" stroke-width="1.6"/><path d="M1 21c0-5 4-8 8-8s6 2 7 4" fill="none" stroke="#111" stroke-width="1.6"/><circle cx="16.5" cy="18.5" r="4.5" fill="var(--blue)"/><rect x="14.5" y="18" width="4" height="3" fill="#fff"/><path d="M15.3 18v-1.2a1.2 1.2 0 0 1 2.4 0V18" stroke="#fff" fill="none"/></svg>
    <span>Customer Log in</span>
    <svg width="22" height="22" viewBox="0 0 22 22" fill="none" stroke="#111" stroke-width="1.2"><path d="M1 5V1h4M17 1h4v4M21 17v4h-4M5 21H1v-4"/><path d="M6 12a5 5 0 0 1 10 0v2M8 13a3 3 0 0 1 6 0v3M11 12v5M6 15v1M16 16v1"/><path d="M7 7a6 6 0 0 1 8 0"/></svg>
  </div>

  <p class="abs credit">Created and research by British Firefighters.</p>
</section>

<!-- Screen 2: dashboard -->
<section class="screen screen--dashboard">
  <div class="abs title-badge" style="left:79px">
    <svg width="18" height="14" viewBox="0 0 18 14" fill="none" stroke="#fff" stroke-width="1.5"><path d="M1 13a8 8 0 0 1 16 0z"/><path d="M9 12l2-6"/></svg>
  </div>
  <h1 class="abs screen-title" style="left:118px">DASHBOARD</h1>

  <svg class="abs" style="left:0;top:0" width="285" height="200"><path d="M140 118 110 148M162 118 190 148" stroke="#cfcac6" stroke-width="1"/></svg>
  <div class="abs node node--start">
    <svg width="26" height="26" viewBox="0 0 26 26"><path d="M10 2h6v8h8v6h-8v8h-6v-8H2v-6h8z" fill="none" stroke="var(--red)" stroke-width="1.6"/></svg>
  </div>
  <p class="abs node-label" style="left:91px;top:126px">START FIRE RISK ASSESSMENT</p>
  <div class="abs node node--commercial">
    <svg width="28" height="30" viewBox="0 0 28 30" fill="none" stroke="#333" stroke-width="1.2"><rect x="3" y="8" width="10" height="21"/><rect x="13" y="2" width="12" height="27"/><path d="M5 12h2M9 12h2M5 16h2M9 16h2M5 20h2M9 20h2M16 6h2M20 6h2M16 10h2M20 10h2M16 14h2M20 14h2M16 18h2M20 18h2M17 29v-5h4v5"/></svg>
  </div>
  <p class="abs node-label" style="left:16px;top:204px">Commercial</p>
  <div class="abs node node--residential">
    <svg width="30" height="28" viewBox="0 0 30 28" fill="none" stroke="#333" stroke-width="1.2"><path d="M1 14 8 8l7 6v12H1z"/><path d="M11 10 20 2l9 8v16H15"/><rect x="5" y="19" width="4" height="7"/><rect x="18" y="19" width="5" height="7"/><rect x="18" y="11" width="5" height="4"/></svg>
  </div>
  <p class="abs node-label" style="left:167px;top:204px">Residential</p>

  <div class="abs status-pill" style="top:257px">COMPLETE
    <svg width="15" height="15" viewBox="0 0 15 15" fill="none" stroke="#222" stroke-width="1.2"><path d="M13 6.5A6 6 0 1 1 9 1.5"/><path d="M4.5 7l2.5 2.5L14 2"/></svg>
  </div>
  <p class="abs entry" style="top:299px">HOLLOWAY BARBERS</p>

  <div class="abs status-pill" style="top:338px">IN PROGRESS
    <svg width="17" height="17" viewBox="0 0 17 17" fill="none" stroke="#222" stroke-width="1.2"><path d="M3 5a7 7 0 0 1 12 3M14 12a7 7 0 0 1-12-3"/><path d="M15 3v5h-5M2 14V9h5"/><path d="M7 5h3L7 12h3"/></svg>
  </div>
  <p class="abs entry" style="top:380px">ELM LANE SCHOOL</p>
  <p class="abs entry" style="top:401px">BRAMBLE NURSING HOME</p>

  <div class="abs status-pill" style="top:444px">PURCHASES
    <svg width="16" height="17" viewBox="0 0 16 17" fill="none" stroke="#222" stroke-width="1.2"><path d="M1 5h11v11H1z"/><path d="M4 5V3a2.5 2.5 0 0 1 5 0v2"/><path d="M10 9l4 1v3c0 2-2 3-2 3s-2-1-2-3z" fill="#f7f5f3"/></svg>
  </div>
  <p class="abs entry" style="top:486px">RESIDENTIAL FIRE RISK ASSESSMENT</p>
  <p class="abs entry" style="top:508px">COMMERCIAL FIRE RISK ASSESSMENT</p>
  <p class="abs entry" style="top:531px">COMMERCIAL FIRE RISK ASSESSMENT</p>

  <nav class="abs tab-bar">
    <div class="abs tab tab--active" style="left:50px;top:17px">
      <svg width="22" height="16" viewBox="0 0 22 16" fill="none" stroke="#fff" stroke-width="1.3"><path d="M1 15a10 10 0 0 1 20 0z"/><path d="M11 13l2-7M4 11h1M17 11h1M6 6l1 1M16 6l-1 1M11 4v1"/></svg>
    </div>
    <div class="abs tab" style="left:118px;top:17px">
      <svg width="20" height="22" viewBox="0 0 20 22" fill="none" stroke="#333" stroke-width="1.2"><path d="M2 1h12v20H2z"/><path d="M14 5h4v16H6"/><path d="M5 5h6M5 9h6M5 13h6M5 17h6"/></svg>
    </div>
    <div class="abs tab" style="left:179px;top:17px">
      <svg width="24" height="22" viewBox="0 0 24 22" fill="none" stroke="#333" stroke-width="1.2"><circle cx="12" cy="4" r="2.5"/><circle cx="7" cy="7" r="2.5"/><circle cx="17" cy="7" r="2.5"/><circle cx="12" cy="10" r="2.5"/><path d="M1 10c2 4 5 8 11 11 6-3 9-7 11-11M4 9c1 4 4 7 8 9 4-2 7-5 8-9"/></svg>
    </div>
    <div class="abs tab" style="left:244px;top:17px">
      <svg width="28" height="20" viewBox="0 0 28 20" fill="none" stroke="#333" stroke-width="1.3"><rect x="1" y="1" width="16" height="18"/><circle cx="10" cy="4.5" r="1.5" fill="#333"/><path d="M9 7l-3 4h3l2 3-2 4M9 7l3 4 3-1M6 15l-3 2"/><path d="M20 7h7M24 4l3 3-3 3"/></svg>
    </div>
  </nav>
</section>

<!-- Screen 3: technical support -->
<section class="screen screen--support">
  <div class="abs title-badge" style="left:32px">
    <svg width="18" height="18" viewBox="0 0 18 18" fill="none" stroke="#fff" stroke-width="1.3"><circle cx="8" cy="7" r="3.5"/><path d="M2 17c0-4 3-6 6-6s6 2 6 6"/><path d="M11 2h6v4h-3l-2 2"/></svg>
  </div>
  <h1 class="abs screen-title" style="left:71px">TECHNICAL SUPPORT</h1>

  <div class="abs reply-box">Type / record you response here
    <svg width="9" height="14" viewBox="0 0 9 14" fill="none" stroke="#333" stroke-width="1.1"><rect x="2.5" y="1" width="4" height="8" rx="2"/><path d="M1 7a3.5 3.5 0 0 0 7 0M4.5 10.5V13M2.5 13h4"/></svg>
  </div>
  <div class="abs send-btn">SEND</div>

  <nav class="abs tab-bar">
    <div class="abs tab" style="left:50px;top:17px">
      <svg width="26" height="18" viewBox="0 0 26 18" fill="none" stroke="#333" stroke-width="1.3"><path d="M1 17a12 12 0 0 1 24 0z"/><path d="M13 15l2-8M5 13h1M20 13h1M7 7l1 1M19 7l-1 1M13 5v1"/></svg>
    </div>
    <div class="abs tab" style="left:118px;top:17px">
      <svg width="20" height="22" viewBox="0 0 20 22" fill="none" stroke="#333" stroke-width="1.2"><path d="M2 1h12v20H2z"/><path d="M14 5h4v16H6"/><path d="M5 5h6M5 9h6M5 13h6M5 17h6"/></svg>
    </div>
    <div class="abs tab tab--active" style="left:166px;top:17px">
      <svg width="24" height="22" viewBox="0 0 24 22" fill="none" stroke="#fff" stroke-width="1.2"><circle cx="12" cy="4" r="2.5"/><circle cx="7" cy="7" r="2.5"/><circle cx="17" cy="7" r="2.5"/><circle cx="12" cy="10" r="2.5"/><path d="M1 10c2 4 5 8 11 11 6-3 9-7 11-11M4 9c1 4 4 7 8 9 4-2 7-5 8-9"/></svg>
    </div>
    <div class="abs tab" style="left:231px;top:17px">
      <svg width="28" height="20" viewBox="0 0 28 20" fill="none" stroke="#333" stroke-width="1.3"><rect x="1" y="1" width="16" height="18"/><circle cx="10" cy="4.5" r="1.5" fill="#333"/><path d="M9 7l-3 4h3l2 3-2 4M9 7l3 4 3-1M6 15l-3 2"/><path d="M20 7h7M24 4l3 3-3 3"/></svg>
    </div>
  </nav>
</section>

</body>
</html>
```